Need a design package for hair towels wrap

We need package design for hair towel wrap ( 3 pack) brand name is The Kovira. We are looking for simple, contemporary and unique design, color palette 2-3 colors. Paper Box size is 9*8*3 inches with PVC window.Actual picture of the product won't be on the package.Attached Brand Logo and description for the package. Barcode needed to be included on the design package.It will be provided later. Attached sample of the box from manufacturer, and instruction for towel wrap which idea I like, if you could make something similar to it, would be great.

Target Market(s)

Brellmart

Industry/Entity Type

Hair

Colors
848484
f5f5f5
faa54b
333333

Requirements
Must have
• Clean, contemporary design.

```html
<!DOCTYPE html>
<html lang="en">
<head>
<meta charset="utf-8">
<title>The Kovira – Microfiber Hair Towel Wrap Box</title>
<link href="https://fonts.googleapis.com/css2?family=Lato:wght@300;400;700;900&display=swap" rel="stylesheet">
<style>
  :root {
    --stage: #e9e9ea;
    --panel-light: #f5f5f5;
    --panel-mid: #e2e3e4;
    --gold-light: #e2b252;
    --gold-deep: #c48f2c;
    --gold-pale: #f6dca0;
    --accent-orange: #faa54b;
    --ink: #333333;
    --ink-soft: #4a4a4a;
    --grey: #848484;
    --towel-light: #e4e6e6;
    --towel-mid: #cfd2d2;
  }
  * { margin: 0; padding: 0; box-sizing: border-box; }
  html, body {
    width: 1200px; height: 900px; overflow: hidden;
    background: var(--stage);
    font-family: "Lato", sans-serif;
  }

  /* Top flap */
  .box-top {
    position: absolute; left: 310px; top: 100px;
    width: 640px; height: 90px;
    background: linear-gradient(180deg, var(--gold-deep) 0%, var(--gold-light) 100%);
    display: flex; align-items: center; justify-content: center;
  }
  .box-top .top-brand {
    font-weight: 900; font-size: 20px; letter-spacing: 2px;
    color: var(--gold-pale);
  }

  /* Side panel */
  .box-side {
    position: absolute; left: 200px; top: 190px;
    width: 110px; height: 580px;
    background: linear-gradient(180deg, var(--panel-light) 0%, var(--panel-mid) 100%);
    padding: 22px 10px 18px 10px;
    color: var(--ink);
    display: flex; flex-direction: column;
  }
  .feature-list { list-style: none; }
  .feature-list li {
    position: relative;
    padding-left: 12px; margin-bottom: 26px;
    font-size: 11px; line-height: 1.35;
  }
  .feature-list li::before {
    content: ""; position: absolute; left: 0; top: 4px;
    width: 6px; height: 6px; background: var(--accent-orange);
  }
  .material-note {
    margin-top: auto;
    font-size: 10px; line-height: 1.3; color: var(--grey);
  }

  /* Front panel */
  .box-front {
    position: absolute; left: 310px; top: 190px;
    width: 640px; height: 580px;
    overflow: hidden;
    background: linear-gradient(180deg, var(--panel-light) 0%, var(--panel-mid) 100%);
    color: var(--ink);
    text-align: center;
  }
  .gold-field {
    position: absolute; left: 0; right: 0; top: 340px; bottom: 0;
    background: linear-gradient(180deg, var(--gold-light) 0%, var(--gold-deep) 100%);
  }
  .brand-mark {
    position: absolute; left: 50%; top: 40px;
    width: 28px; height: 28px; margin-left: -14px;
    background: var(--gold-deep);
  }
  .brand-name {
    position: absolute; left: 0; right: 0; top: 88px;
    font-weight: 900; font-size: 33px; letter-spacing: 0.5px;
  }
  .product-title {
    position: absolute; left: 0; right: 0; top: 140px;
    font-weight: 300; font-size: 37px; letter-spacing: 0.5px;
  }
  .product-window {
    position: absolute; left: 48px; top: 212px;
    width: 544px; height: 250px;
    border: 4px solid var(--accent-orange);
    border-radius: 22px;
    background: linear-gradient(90deg, var(--towel-light) 0%, var(--towel-mid) 33%, var(--towel-light) 50%, var(--towel-mid) 66%, var(--towel-light) 100%);
  }
  .pack-count {
    position: absolute; left: 0; right: 0; top: 476px;
    font-weight: 900; font-size: 27px;
  }
  .tagline {
    position: absolute; left: 0; right: 0; top: 514px;
    font-weight: 400; font-size: 20px; line-height: 1.25;
    color: var(--ink-soft);
  }
</style>
</head>
<body>
  <div class="box-top">
    <span class="top-brand">THE KOVIRA</span>
  </div>

  <aside class="box-side">
    <ul class="feature-list">
      <li>Fits all head sizes.</li>
      <li>Suitable for all hair types and lengths, holds extra long hair.</li>
      <li>Absorbs approximately 70% of the water within 10 min.</li>
      <li>Less time blow drying means healthier hair.</li>
      <li>Reduces risk of split ends, breakage and frizz.</li>
    </ul>
    <p class="material-note">Microfiber 100% polyester</p>
  </aside>

  <main class="box-front">
    <div class="gold-field" role="img" aria-label="Gold band with a faint repeating brand pattern"></div>
    <div class="brand-mark"></div>
    <h1 class="brand-name">THE KOVIRA</h1>
    <h2 class="product-title">MICROFIBER HAIR TOWEL WRAP</h2>
    <div class="product-window" role="img" aria-label="Clear window showing three rolled white microfiber hair towels"></div>
    <p class="pack-count">Set of 3 Hair Towels</p>
    <p class="tagline">The softest, ultra-absorbent, light &amp; safest<br>Towel for your beautiful hair.</p>
  </main>
</body>
</html>
```